Simple and Clean business card design

We would like the design to be simple clean and to incorporate our colors.

We are open to your design and talent, we have the dots in our logo as we think of it as data points and we connect data points for people.

We are open to see the great creative and clean design you bring to the table

Contact Information for Business Card

please include: name, position, email, phone and website

Font styles to use
Sans Serif

Requirements
Must have
• my colors incorporated, simplicity
Nice to have
• lots of white space, simplicity
Should not have
• complexicity/ complex art

```html
<!DOCTYPE html>
<html lang="en">
<head>
<meta charset="utf-8">
<title>Nectra Business Card</title>
<link rel="stylesheet" href="https://fonts.googleapis.com/css2?family=Oswald:wght@500&family=Work+Sans:wght@400;600&display=swap">
<style>
  :root {
    --bg: #1b1b1c;
    --card: #242425;
    --card-edge: #2e2e30;
    --silver: #c9c9cb;
    --silver-soft: #9a9a9d;
    --text: #e4e4e6;
    --brand-blue: #5a7fc6;
  }
  * { margin: 0; padding: 0; box-sizing: border-box; }
  html, body {
    width: 1200px; height: 900px; overflow: hidden;
    background: var(--bg);
  }
  .canvas {
    width: 1200px; height: 900px;
    display: flex; flex-direction: column;
    align-items: center; justify-content: center; gap: 34px;
  }
  .card {
    width: 640px; height: 366px;
    background: linear-gradient(135deg, var(--card) 0%, #2b2b2d 70%, #303032 100%);
    border: 1px solid var(--card-edge);
    box-shadow: 0 18px 40px rgba(0,0,0,.55);
    position: relative;
  }
  .card--front {
    display: flex; align-items: center; justify-content: center;
  }
  .brand {
    display: flex; align-items: center; gap: 16px;
  }
  .brand__dot {
    width: 22px; height: 22px; border-radius: 50%;
    background: var(--brand-blue);
  }
  .brand__name {
    font-family: "Work Sans", sans-serif;
    font-weight: 600; font-size: 96px; letter-spacing: -1px;
    color: var(--silver);
    line-height: 1;
  }
  .card--back {
    display: flex; align-items: center;
    padding: 0 40px 0 60px;
  }
  .identity {
    width: 230px; text-align: right; padding-right: 24px;
  }
  .identity__name {
    font-family: "Oswald", sans-serif;
    font-weight: 500; font-size: 34px; letter-spacing: 1.5px;
    color: var(--silver); text-transform: uppercase; line-height: 1.1;
  }
  .identity__role {
    font-family: "Work Sans", sans-serif;
    font-size: 16px; letter-spacing: 1px;
    color: var(--silver-soft); margin-top: 4px;
  }
  .divider {
    width: 2px; height: 110px; background: var(--silver-soft);
  }
  .contact {
    padding-left: 30px;
    font-family: "Work Sans", sans-serif;
    font-size: 17px; color: var(--text); line-height: 1.4;
    list-style: none;
  }
  .contact__item { display: flex; align-items: center; gap: 8px; }
  .contact__item svg { width: 14px; height: 14px; flex: none; }
  .contact__address { margin-bottom: 6px; }
</style>
</head>
<body>
<main class="canvas">
  <section class="card card--front">
    <div class="brand">
      <span class="brand__dot"></span>
      <span class="brand__name">Nectra</span>
    </div>
  </section>

  <section class="card card--back">
    <div class="identity">
      <p class="identity__name">Daniel Reyes</p>
      <p class="identity__role">Founder</p>
    </div>
    <div class="divider"></div>
    <ul class="contact">
      <li class="contact__address">418 Cedar Bend Lane<br>Marlow, TX 75460</li>
      <li class="contact__item">
        <svg viewBox="0 0 16 16" fill="none" stroke="currentColor" stroke-width="1.6"><path d="M4 1.5h2.5l1 3.5-1.8 1.2a8 8 0 0 0 4.1 4.1L11 8.5l3.5 1V12a2 2 0 0 1-2 2A11 11 0 0 1 2 3.5a2 2 0 0 1 2-2z"/></svg>
        0412 598 203
      </li>
      <li class="contact__item">
        <svg viewBox="0 0 16 16" fill="none" stroke="currentColor" stroke-width="1.4"><rect x="1.5" y="3.5" width="13" height="9" rx="1"/><path d="M1.5 4l6.5 5 6.5-5"/></svg>
        info@brightlattice.com
      </li>
      <li class="contact__item">
        <svg viewBox="0 0 16 16" fill="none" stroke="currentColor" stroke-width="1.3"><circle cx="8" cy="8" r="6.5"/><ellipse cx="8" cy="8" rx="2.8" ry="6.5"/><path d="M1.5 8h13M2.5 5h11M2.5 11h11"/></svg>
        www.brightlattice.com
      </li>
    </ul>
  </section>
</main>
</body>
</html>
```